Business card design

I am open to ideas. I was thinking of a vertical design, turning the name 90 degrees and placing it on the left edge, then some clipped portion of the fabulous tree with contact info on the bottom -- special emphasis on Web address:WhimBeads.comFor All Your Beading Needs121 E. Cotati AveCotati, CA 94931(707) 664-8343

```html
<!DOCTYPE html>
<html lang="en">
<head>
<meta charset="utf-8">
<title>Fern &amp; Glass business card</title>
<link href="https://fonts.googleapis.com/css2?family=Roboto:wght@400;500;700&family=Roboto+Condensed:wght@700&display=swap" rel="stylesheet">
<style>
  :root {
    --backdrop: #3b3b3d;
    --card-black: #050505;
    --card-white: #ffffff;
    --ink: #2b2b2b;
    --text-light: #f2f2f2;
    --violet: #6a3aa8;
    --blue: #1f6fc4;
    --leaf-green: #7cc242;
    --green: #2f9a3c;
    --yellow: #f4c21a;
    --orange: #f07a1e;
    --red: #e5261f;
  }
  * { margin: 0; padding: 0; box-sizing: border-box; }
  html, body { width: 1200px; height: 896px; overflow: hidden; }
  body {
    background: var(--backdrop);
    font-family: "Roboto", Arial, sans-serif;
    display: flex;
    flex-direction: column;
    align-items: center;
    justify-content: center;
    gap: 36px;
  }
  .card {
    position: relative;
    width: 700px;
    height: 400px;
    overflow: hidden;
    box-shadow: 0 10px 28px rgba(0,0,0,0.45);
  }

  /* Contact side */
  .card-contact { background: var(--card-white); }
  .contact-band {
    position: absolute;
    left: 0; right: 0; bottom: 0;
    height: 128px;
    background: var(--card-black);
  }
  .tree-art {
    position: absolute;
    right: -30px;
    top: 40px;
    width: 430px;
    height: 330px;
    border-radius: 48% 52% 40% 44% / 55% 55% 40% 40%;
    background: linear-gradient(100deg, var(--violet) 0%, var(--blue) 32%, var(--green) 55%, var(--leaf-green) 70%, var(--yellow) 84%, var(--orange) 100%);
  }
  .contact-list {
    position: absolute;
    left: 52px;
    top: 44px;
    list-style: none;
    color: var(--ink);
  }
  .contact-item { display: flex; align-items: center; gap: 16px; margin-bottom: 18px; }
  .contact-item svg { flex: none; }
  .phone { font-size: 30px; font-weight: 700; letter-spacing: 1px; }
  .address { font-size: 22px; font-weight: 500; line-height: 1.2; }
  .web {
    position: absolute;
    left: 52px;
    bottom: 40px;
    font-family: "Roboto Condensed", "Arial Narrow", sans-serif;
    font-weight: 700;
    font-size: 44px;
    letter-spacing: 0.5px;
  }
  .web-prefix { color: var(--violet); }
  .web-name { color: var(--leaf-green); }
  .web-suffix { color: var(--red); }

  /* Brand side */
  .card-brand {
    background: var(--card-black);
    display: flex;
    flex-direction: column;
    align-items: center;
    justify-content: center;
    color: var(--text-light);
  }
  .brand-mark { display: flex; align-items: center; gap: 16px; }
  .brand-dot {
    width: 22px; height: 22px;
    border-radius: 50%;
    background: var(--leaf-green);
  }
  .brand-name { font-size: 58px; font-weight: 400; letter-spacing: 1px; }
  .tagline {
    margin-top: 18px;
    font-size: 19px;
    font-weight: 400;
    letter-spacing: 2px;
    text-transform: uppercase;
  }
</style>
</head>
<body>

  <section class="card card-contact">
    <div class="contact-band"></div>
    <div class="tree-art" role="img" aria-label="Illustrated tree with rainbow leaves and a hanging swing"></div>
    <ul class="contact-list">
      <li class="contact-item">
        <svg width="34" height="34" viewBox="0 0 34 34" aria-hidden="true">
          <circle cx="17" cy="17" r="15" fill="none" stroke="#2b2b2b" stroke-width="2.5"/>
          <path d="M13 10 q-3 7 3 14 l3 -2 q-4 -4 -3 -9 z" fill="#2b2b2b"/>
        </svg>
        <span class="phone">(707) 555-0192</span>
      </li>
      <li class="contact-item">
        <svg width="34" height="34" viewBox="0 0 34 34" aria-hidden="true">
          <circle cx="17" cy="17" r="15" fill="none" stroke="#2b2b2b" stroke-width="2.5"/>
          <path d="M17 8 a6 6 0 0 1 6 6 c0 5 -6 11 -6 11 s-6 -6 -6 -11 a6 6 0 0 1 6 -6 z" fill="#2b2b2b"/>
          <circle cx="17" cy="14" r="2.2" fill="#fff"/>
        </svg>
        <span class="address">348 W. Brindle Ave<br>Halden, CA 94958</span>
      </li>
    </ul>
    <p class="web"><span class="web-prefix">www.</span><span class="web-name">FernGlassco</span><span class="web-suffix">.com</span></p>
  </section>

  <section class="card card-brand">
    <div class="brand-mark">
      <span class="brand-dot"></span>
      <span class="brand-name">Fern &amp; Glass</span>
    </div>
    <p class="tagline">For all your beading needs</p>
  </section>

</body>
</html>
```